Best Seller Cover Design for Inspirational Non-Fiction, Self-Help Book

I've been working diligently on a book title "Quiet Harbor Rising" that will be pivotal for my coaching business. We're heavily investing in marketing and public relations for this and would love it to be a best seller (every other's dream). I need an amazing book cover design that is eye-catching, description, creative, interesting, and compelling, Can you work your magic?I've attached a detailed description along with the content for the back cover. Please let me know if all the content does not fit and I'm happy to reduce it. I need a cover that sells and speaks to the description, whatever you think that will be best. Book DetailsTitle: Self-Defined SuccessSubtitle: Spoiler Alert: You Already Have Everything It TakesAuthor: Ngan H. NguyenSpecifics:- The book will be 5.5" by 8.5" and 216 pages (may change slightly and we can update the spine in final revisions). - Paperback and leave space for a bar code- Will need the raw files so this can be redesigned into hardcover down the line- Orvello book cover upload ready- Final file will also need the front cover only for e-book version- Add profile headshot (attached) to back-cover if space permits.I do not have a clear vision of what will be best for this cover but I really like the evocative style of Colin Ferraway Plenitude book. Thank you!

Target Market(s)

Professionals in transition, aspiring or new entrepreneurs, change-makers.

Font styles to use
Serif
Script

Colors

Designer to choose colors to be used in the design.

Requirements
Must have
• Traditional but with elements that make it interesting and provocative since it is speaking to a twist on a topic that has been well talked about, success.

```html
<!DOCTYPE html>
<html lang="en">
<head>
<meta charset="utf-8">
<title>Quiet Harbor Rising – Cover Wrap</title>
<link rel="stylesheet" href="https://fonts.googleapis.com/css2?family=Oswald:wght@300;400;500;700&family=Open+Sans:ital,wght@0,400;0,600;1,700&display=swap">
<style>
  :root {
    --page-bg: #e4e4e2;
    --cover-top: #433d44;
    --cover-bottom: #2f2a30;
    --accent-yellow: #f7c81a;
    --chalk-orange: #f0a13a;
    --text-light: #f2f0f2;
    --text-body: #e6e3e7;
    --photo-tone: #5a4a44;
  }
  * { margin: 0; padding: 0; box-sizing: border-box; }
  html, body {
    width: 1200px; height: 800px; overflow: hidden;
    background: var(--page-bg);
  }
  .cover-wrap {
    position: absolute; left: 133px; top: 60px;
    display: flex; height: 680px;
    box-shadow: 0 10px 30px rgba(0,0,0,.18);
  }
  .panel {
    background: linear-gradient(180deg, var(--cover-top), var(--cover-bottom));
    height: 100%; position: relative;
  }
  /* Back cover */
  .back-cover { width: 440px; padding: 38px 38px 0 40px; color: var(--text-body); font-family: "Open Sans", sans-serif; }
  .back-headline {
    color: var(--accent-yellow); font-weight: 600; font-size: 12.5px;
    text-align: center; margin-bottom: 12px;
  }
  .back-copy p {
    font-size: 11.2px; line-height: 1.42; text-align: justify; margin-bottom: 9px;
  }
  .author-bio { margin-top: 16px; font-size: 11.2px; line-height: 1.42; text-align: justify; }
  .author-photo {
    float: left; width: 100px; height: 118px; margin: 3px 12px 4px 0;
    background: linear-gradient(160deg, #6e625c, var(--photo-tone) 60%, #3a302d);
  }
  .author-bio strong { font-style: italic; font-weight: 700; color: var(--text-light); }
  /* Spine */
  .spine {
    width: 52px; border-left: 1px solid rgba(0,0,0,.35); border-right: 1px solid rgba(0,0,0,.35);
    display: flex; flex-direction: column; align-items: center; padding-top: 30px;
    font-family: "Oswald", sans-serif;
  }
  .spine span { writing-mode: vertical-rl; font-size: 27px; letter-spacing: 1px; line-height: 1; }
  .spine-title { color: var(--accent-yellow); font-weight: 500; }
  .spine-author { color: var(--text-light); font-weight: 500; margin-top: 40px; }
  /* Front cover */
  .front-cover { width: 440px; overflow: hidden; font-family: "Oswald", sans-serif; }
  .title-top {
    position: absolute; top: 48px; left: 0; width: 100%; text-align: center;
    color: var(--text-light); font-weight: 300; font-size: 64px; letter-spacing: 4px; line-height: 1;
  }
  .title-main {
    position: absolute; top: 118px; left: 0; width: 100%; text-align: center;
    color: var(--accent-yellow); font-weight: 700; font-size: 132px; line-height: 1; letter-spacing: 2px;
  }
  .tagline-band {
    position: absolute; top: 290px; left: 0; width: 100%;
    border-top: 2px solid var(--accent-yellow); border-bottom: 2px solid var(--accent-yellow);
    padding: 11px 0; text-align: center; color: var(--text-light);
    font-size: 14.5px; font-weight: 400; letter-spacing: .2px;
  }
  .tagline-band b { font-weight: 700; }
  .cover-illustration { position: absolute; left: 0; bottom: 0; width: 100%; height: 300px; }
  .author-name {
    position: absolute; bottom: 42px; left: 0; width: 100%; text-align: center;
    color: var(--text-light); font-weight: 500; font-size: 40px; letter-spacing: 2px;
  }
</style>
</head>
<body>
<div class="cover-wrap">
  <section class="panel back-cover">
    <h2 class="back-headline">When all is said and done, what will matter to you most?</h2>
    <div class="back-copy">
      <p>Following someone else’s path or society’s definition of “success” doesn’t often lead to personal fulfillment. At the end of the day, we genuinely want to succeed—not live a life defined by others.</p>
      <p>You can achieve anything you desire, and when you aim high for your spark of passion you will succeed. Passion is what awakens the heart, fires the soul, and fills the spirit. It is passion that energizes and sparks the pull forward through all barriers, uncertainty, and challenges.</p>
      <p>On this journey, we are asked to turn inward and search for the invisible, the hidden, and the sacred possibilities in order to claim what is ours in truth. We will then fill that shell with a desire that will ignite its creation.</p>
      <p>May this book serve as your guide on how to evoke this clarity and desire for your most authentic path enabling you to create a vision for your future that will bring you the ultimate sense of fulfillment. In addition, this book will show you the steps to navigate the path forward toward this new dream giving you the opportunity to awaken innate abilities you didn’t know you had that will open the door to success.</p>
    </div>
    <div class="author-bio">
      <div class="author-photo" role="img" aria-label="Author headshot"></div>
      <strong>Mira T. Larkspur</strong> has built her platform of a vision-driven life after 10 years of experience working as a business strategy advisor in Meridian 500 companies and at Halloway &amp; Reed. Combining her advisory experience with her passion for spiritual principles of success, she now empowers entrepreneurs, change-makers, and leaders to step into their truth and bring their unique vision to life. Enabling them to change their lives, revolutionize their work, create greater impact in the world.
    </div>
  </section>

  <aside class="panel spine">
    <span class="spine-title">QUIET HARBOR RISING</span>
    <span class="spine-author">MIRA T. LARKSPUR</span>
  </aside>

  <section class="panel front-cover">
    <svg class="cover-illustration" viewBox="0 0 440 300" preserveAspectRatio="none" role="img" aria-label="Hand drawing a rising orange chalk arrow out of a scatter of small arrows on a chalkboard">
      <defs>
        <radialGradient id="chalkGlow" cx="45%" cy="55%" r="60%">
          <stop offset="0" stop-color="#f0a13a" stop-opacity=".35"/>
          <stop offset="1" stop-color="#2f2a30" stop-opacity="0"/>
        </radialGradient>
        <linearGradient id="handTone" x1="0" y1="0" x2="0" y2="1">
          <stop offset="0" stop-color="#c99a80" stop-opacity=".35"/>
          <stop offset="1" stop-color="#a9775e" stop-opacity=".5"/>
        </linearGradient>
      </defs>
      <rect width="440" height="300" fill="url(#chalkGlow)"/>
      <rect x="350" y="40" width="90" height="260" fill="url(#handTone)"/>
    </svg>
    <div class="title-top">QUIET HARBOR</div>
    <div class="title-main">RISING</div>
    <div class="tagline-band"><b>PLOT TWIST:</b> THE MAP WAS ALWAYS INSIDE YOUR POCKET</div>
    <div class="author-name">MIRA T. LARKSPUR</div>
  </section>
</div>
</body>
</html>
```